Design a web site for my business - Brightline Coatings Co.

We are a family business that handles design, fabrication and installation of powder coated aluminum, stainless steel and glass products. Including handrails, privacy slat screens, electric gates and pool fencing. We are based in the Whitsundays in North Queensland and service an area from Airlie Beach to Townsville.

Target Market(s)

Domestic and commercial

Industry/Entity Type

fabrication - manufacturing

Coding

Coded - Design and coding required

Number of Pages Required

5+ page

Colors
0054AA
0677BA
7BADD7
CADEEF
E8F1F8

Requirements
Must have
• photo galleries, contact page, one page for privacy screens, balustrades, glass fencing, stainless steel handrail, powder coated aluminium handrails and pool fencing

```html
<!DOCTYPE html>
<html lang="en">
<head>
<meta charset="utf-8">
<title>Brightline Coatings Co — Aluminium, Stainless Steel &amp; Glass Fabrication</title>
<link rel="stylesheet" href="https://fonts.googleapis.com/css2?family=Plus+Jakarta+Sans:wght@400;500;600;700&display=swap">
<style>
  :root {
    --blue: #0054AA;
    --blue-mid: #0677BA;
    --blue-soft: #7BADD7;
    --blue-pale: #CADEEF;
    --blue-mist: #E8F1F8;
    --navy: #141b2b;
    --ink: #1a1f2b;
    --white: #ffffff;
    --muted: #c7ccd6;
    --page-bg: #dfe5ea;
  }
  * { box-sizing: border-box; margin: 0; padding: 0; }
  html, body {
    width: 1200px; height: 900px; overflow: hidden;
    background: var(--page-bg);
    font-family: "Plus Jakarta Sans", sans-serif;
    color: var(--ink);
  }
  .site { width: 1200px; height: 900px; position: relative; background: var(--white); overflow: hidden; }

  .site-header {
    height: 104px; display: flex; align-items: center;
    padding: 0 90px; background: var(--white);
  }
  .brand { display: flex; align-items: center; gap: 10px; font-weight: 700; font-size: 17px; color: var(--ink); }
  .brand-square { width: 14px; height: 14px; background: var(--blue); }
  .main-nav { display: flex; gap: 34px; margin-left: auto; margin-right: 70px; font-size: 14px; font-weight: 500; color: #3a4150; }
  .header-phone { display: flex; align-items: center; gap: 8px; color: var(--blue); font-size: 14px; font-weight: 600; margin-right: 24px; }
  .btn { display: inline-flex; align-items: center; justify-content: center; font-weight: 600; font-size: 14px; text-decoration: none; }
  .btn-primary { background: var(--blue); color: var(--white); }
  .btn-outline { border: 1.5px solid rgba(255,255,255,.55); color: var(--white); }
  .header-cta { width: 112px; height: 46px; box-shadow: 0 4px 10px rgba(0,84,170,.25); }

  .hero { position: relative; height: 620px; }
  .hero-photo {
    position: absolute; inset: 0;
    background:
      linear-gradient(90deg, rgba(20,27,43,.94) 0%, rgba(20,27,43,.75) 45%, rgba(20,27,43,.35) 100%),
      linear-gradient(160deg, #3a3230 0%, #262b38 40%, #1b2231 70%, #2b3340 100%);
  }
  .hero-content { position: relative; padding: 150px 0 0 120px; width: 760px; }
  .hero-eyebrow {
    display: inline-block; border: 1px solid rgba(255,255,255,.4);
    padding: 7px 12px; font-size: 11px; font-weight: 700; letter-spacing: .09em;
    text-transform: uppercase; color: var(--white);
  }
  .hero-title { margin-top: 30px; font-size: 58px; line-height: 1.1; font-weight: 700; letter-spacing: -.02em; color: var(--white); }
  .hero-text { margin-top: 24px; font-size: 16px; line-height: 1.65; color: var(--muted); max-width: 520px; }
  .hero-actions { margin-top: 34px; display: flex; gap: 16px; }
  .hero-actions .btn { height: 52px; padding: 0 30px; font-size: 15px; }

  .stats {
    position: absolute; left: 120px; right: 120px; top: 690px;
    display: grid; grid-template-columns: repeat(4, 1fr); gap: 8px;
  }
  .stat {
    background: var(--white); height: 78px; display: flex; align-items: center; justify-content: center;
    font-size: 20px; font-weight: 600; color: var(--ink);
    box-shadow: 0 10px 24px rgba(20,27,43,.15); border-left: 3px solid var(--blue);
  }

  .story { position: absolute; left: 120px; top: 808px; }
  .story-eyebrow { font-size: 11px; font-weight: 700; letter-spacing: .12em; text-transform: uppercase; color: var(--blue-mid); }
  .story-title { margin-top: 8px; font-size: 30px; font-weight: 700; letter-spacing: -.01em; color: var(--ink); }
</style>
</head>
<body>
<div class="site">
  <header class="site-header">
    <div class="brand"><span class="brand-square"></span>Brightline Coatings Co</div>
    <nav class="main-nav">
      <span>About</span><span>Services</span><span>Gallery</span><span>Contact</span>
    </nav>
    <div class="header-phone">
      <svg width="16" height="16" viewBox="0 0 24 24" fill="none" stroke="currentColor" stroke-width="2" stroke-linecap="round" stroke-linejoin="round"><path d="M22 16.9v3a2 2 0 0 1-2.2 2 19.8 19.8 0 0 1-8.6-3.1 19.5 19.5 0 0 1-6-6A19.8 19.8 0 0 1 2.1 4.2 2 2 0 0 1 4.1 2h3a2 2 0 0 1 2 1.7c.1.9.4 1.8.7 2.7a2 2 0 0 1-.5 2.1L8 9.8a16 16 0 0 0 6 6l1.3-1.3a2 2 0 0 1 2.1-.4c.9.3 1.8.6 2.7.7a2 2 0 0 1 1.7 2z"/></svg>
      (07) 4000 5821
    </div>
    <a class="btn btn-primary header-cta" href="#">Get Quote</a>
  </header>

  <section class="hero">
    <div class="hero-photo" role="img" aria-label="Photo of a timber-decked balcony with powder coated aluminium balustrade under a dark roof"></div>
    <div class="hero-content">
      <span class="hero-eyebrow">North Queensland's Premier Fabricator</span>
      <h1 class="hero-title">Premium Aluminium,<br>Stainless Steel &amp; Glass<br>Fabrication</h1>
      <p class="hero-text">Custom designed, fabricated and professionally installed products for residential and commercial projects across North Queensland. Precision craftsmanship that elevates your architecture.</p>
      <div class="hero-actions">
        <a class="btn btn-primary" href="#">Request a Free Quote</a>
        <a class="btn btn-outline" href="#">View Our Projects</a>
      </div>
    </div>
  </section>

  <div class="stats">
    <div class="stat">20+ Years</div>
    <div class="stat">1000+ Projects</div>
    <div class="stat">Family Owned</div>
    <div class="stat">Fully Licensed</div>
  </div>

  <section class="story">
    <p class="story-eyebrow">Our Story</p>
    <h2 class="story-title">The trusted name in Whitsundays fabrication.</h2>
  </section>
</div>
</body>
</html>
```